Design website for new email startup

We are starting a company called Pingo.QZ (it will live at http://pingo.qz).

We would like the main landing page for our site designed. We have provided a very simple wireframe to help provide direction for the content it should include, but we do not expect the designers to adhere to it at all - we encourage unique ideas. There is some sample text in the wireframe - this does not have to be used, but may provide ideas.

We provide an easy way for people to manage email for a custom domain name. For example if you own "yourhouseword.example" you can point your DNS records to us and we'll make it easy to have emails addressed to your domain get forwarded to your existing email (gmail, etc). Folks running blogs, and other small sites can quickly setup email addresses for their domains and manage them in one place.

(For technical folks, we have you point your dns mx records to us, hence the name. That way all your email hits us and we can redirect it wherever you want. We make it easy to manage a single domain or a bunch of domains. Many domain registrars offer this service for a fee, and have clumsy management tools. We provide a robust simple toolset for free, as well as premium options).

The goal of the landing page is to get folks into the signup flow. The second priority flow is to have them take a look at the premium plan offerings.

We may offer the winning designer additional work for the remainder of the site design.
Updates

I've changed this project to a committed payment.  It is no longer refundable.  Thank you.

Target Market(s)

Bloggers, podcasters, designers, app developers - people who are a little tech savvy.

Industry/Entity Type

It Company

Font styles to use
Sans Serif

Colors

Designer to choose colors to be used in the design.

Requirements
Must have
• A full fidelity mockup (comp) of the landing page including the source file (psd, ai, etc).

Some sort of logo treatment for the pingo.qz brand

A call to action for signup, such as the suggested 'Get Started Here'
Nice to have
• A hip startup feel

Incorporation of the email theme

Give the impression it is simple, easy and fast

```html
<!DOCTYPE html>
<html lang="en">
<head>
<meta charset="utf-8">
<title>Pingo.QZ — We make email easy</title>
<link rel="stylesheet" href="https://fonts.googleapis.com/css2?family=Open+Sans:wght@400;600;700&display=swap">
<style>
  :root {
    --brand-blue: #1a8fd6;
    --brand-blue-dark: #1478b8;
    --button-top: #27a6e6;
    --button-bottom: #1587c9;
    --ink: #333333;
    --muted: #777777;
    --header-bg: #ffffff;
    --hero-dark: #070b16;
    --hero-mid: #0f1b3a;
    --hero-glow: #3a6fd0;
    --footer-bg: #eeeeee;
    --footer-line: #d8d8d8;
    --social: #2f5ea8;
    --social-alt: #28a8e8;
    --dot: #666666;
  }
  * { box-sizing: border-box; margin: 0; padding: 0; }
  html, body { width: 1200px; height: 802px; overflow: hidden; }
  body {
    font-family: "Open Sans", Arial, sans-serif;
    color: var(--ink);
    background: #ffffff;
    position: relative;
  }
  a { text-decoration: none; color: inherit; }

  /* Header */
  .site-header {
    position: absolute; top: 0; left: 0; width: 1200px; height: 81px;
    background: linear-gradient(#ffffff, #f6f6f6);
    border-top: 1px solid #e2e2e2;
    box-shadow: 0 1px 3px rgba(0,0,0,0.15);
    z-index: 2;
  }
  .brand {
    position: absolute; left: 101px; top: 18px;
    font-size: 38px; font-weight: 700; color: var(--brand-blue);
    letter-spacing: -0.5px; line-height: 44px;
  }
  .main-nav {
    position: absolute; right: 100px; top: 31px;
    font-size: 13.5px; text-transform: uppercase; color: var(--ink);
    display: flex; gap: 14px;
  }
  .main-nav .sep { color: #999; }
  .main-nav .is-active { color: var(--brand-blue); }

  /* Hero */
  .hero {
    position: absolute; top: 81px; left: 0; width: 1200px; height: 435px;
    background: var(--hero-dark);
    overflow: hidden;
  }
  .hero-visual {
    position: absolute; right: 0; top: 0; width: 680px; height: 435px;
    background:
      radial-gradient(circle at 290px 180px, rgba(200,225,255,0.9) 0, rgba(90,140,230,0.6) 60px, rgba(40,80,170,0.35) 170px, rgba(15,27,58,0) 330px),
      linear-gradient(90deg, var(--hero-dark) 0%, var(--hero-mid) 35%, #12214a 65%, #0a0f1c 100%);
  }
  .hero-title {
    position: absolute; left: 101px; top: 135px;
    font-size: 32px; font-weight: 400; color: #ffffff;
  }
  .hero-actions { position: absolute; left: 101px; top: 186px; display: flex; gap: 6px; }
  .btn {
    display: inline-block; height: 43px; line-height: 43px; padding: 0 15px;
    font-size: 18.5px; font-weight: 600; text-transform: uppercase; color: #ffffff;
    background: linear-gradient(var(--button-top), var(--button-bottom));
    border-radius: 2px;
  }
  .slider-dots { position: absolute; left: 102px; top: 392px; display: flex; gap: 9px; }
  .slider-dots span {
    width: 14px; height: 14px; border-radius: 50%;
    background: radial-gradient(circle at 40% 35%, #9a9a9a, var(--dot));
  }
  .slider-dots .is-current { background: radial-gradient(circle at 40% 35%, #555, #2a2a2a); }

  /* Features */
  .features {
    position: absolute; top: 516px; left: 0; width: 1200px; height: 204px;
    background: #ffffff;
  }
  .feature { position: absolute; top: 34px; width: 480px; }
  .feature--dns { left: 107px; }
  .feature--registrar { left: 612px; }
  .feature-icon { position: absolute; left: 0; top: 8px; }
  .feature-title {
    margin-left: 94px; font-size: 18.5px; font-weight: 400; line-height: 27px;
    color: var(--brand-blue);
  }
  .feature--registrar .feature-title { margin-left: 65px; }
  .feature-text {
    margin-top: 14px; font-size: 13px; line-height: 23px; color: var(--muted);
  }

  /* Footer */
  .site-footer {
    position: absolute; top: 720px; left: 0; width: 1200px; height: 82px;
    background: var(--footer-bg);
    border-top: 1px solid var(--footer-line);
  }
  .footer-nav {
    position: absolute; left: 101px; top: 16px;
    font-size: 13.5px; color: var(--ink); display: flex; gap: 12px;
  }
  .footer-nav .sep { color: #999; }
  .copyright { position: absolute; left: 101px; top: 44px; font-size: 13.5px; color: var(--ink); }
  .social { position: absolute; left: 1024px; top: 26px; display: flex; gap: 13px; }
  .social span { width: 32px; height: 32px; border-radius: 50%; background: var(--social); }
  .social .social-alt { background: var(--social-alt); }
</style>
</head>
<body>
  <header class="site-header">
    <a class="brand" href="http://pingo.qz">Pingo.QZ</a>
    <nav class="main-nav">
      <a class="is-active" href="#">How it works</a><span class="sep">/</span>
      <a href="#">Support</a><span class="sep">/</span>
      <a href="#">Login</a>
    </nav>
  </header>

  <section class="hero">
    <div class="hero-visual" role="img" aria-label="Photo of a fingertip touching a glowing envelope icon surrounded by floating email icons on a dark blue background"></div>
    <h1 class="hero-title">We make email easy</h1>
    <div class="hero-actions">
      <a class="btn btn--primary" href="#">Get started free</a>
      <a class="btn btn--secondary" href="#">Compare plans</a>
    </div>
    <div class="slider-dots"><span class="is-current"></span><span></span><span></span><span></span></div>
  </section>

  <section class="features">
    <article class="feature feature--dns">
      <svg class="feature-icon" width="80" height="56" viewBox="0 0 80 56" aria-hidden="true">
        <circle cx="40" cy="28" r="26" fill="var(--brand-blue-dark)"/>
      </svg>
      <h2 class="feature-title">How to configure your<br>NimbusEdge DNS to use pingo.qz</h2>
      <p class="feature-text">Aliquam interdum tincidunt erat ac gravida. Nam ut libero viverra, egestas mauris a, suscipit nunc. Phasellus ullamcorper bibendum diam, eget molestie enim. Vivamus pellentesque mi vitae elit fringilla.</p>
    </article>
    <article class="feature feature--registrar">
      <svg class="feature-icon" width="50" height="70" viewBox="0 0 50 70" aria-hidden="true">
        <rect x="2" y="4" width="46" height="62" fill="var(--brand-blue)"/>
      </svg>
      <h2 class="feature-title">Use pingo.qz with your DomainHive domain<br>registration for reliable email forwarding</h2>
      <p class="feature-text">Aliquam interdum tincidunt erat ac gravida. Nam ut libero viverra, egestas mauris a, suscipit nunc. Phasellus ullamcorper bibendum diam, eget molestie enim. Vivamus pellentesque mi vitae elit fringilla.</p>
    </article>
  </section>

  <footer class="site-footer">
    <nav class="footer-nav">
      <a href="#">Home</a><span class="sep">|</span>
      <a href="#">How it works</a><span class="sep">|</span>
      <a href="#">Support</a><span class="sep">|</span>
      <a href="#">Login</a>
    </nav>
    <p class="copyright">Copyright &copy; 2014 Pingo. &nbsp;All rights reserved.</p>
    <div class="social" aria-label="Social links"><span></span><span class="social-alt"></span></div>
  </footer>
</body>
</html>
```